Business Card For Halvenmoor Financial Consulting

Hi, I would like a business card designed. Bold, modern.
Please use the same design as the logo. I have also attached the website design to see the overall theme.
Wordmark Font
Color: Hex: #01AEF7

```html
<!DOCTYPE html>
<html lang="en">
<head>
<meta charset="utf-8">
<title>Halvenmoor Financial Consulting – Business Card</title>
<link rel="stylesheet" href="https://fonts.googleapis.com/css2?family=Montserrat:wght@400;500;700;800&display=swap">
<style>
  :root {
    --backdrop: #3b3b3b;
    --card: #17222d;
    --accent: #01aef7;
    --accent-soft: #4a8fc0;
    --embossed: #0f1821;
    --white: #ffffff;
    --muted: #dfe6ec;
  }
  * { box-sizing: border-box; margin: 0; padding: 0; }
  html, body {
    width: 1200px; height: 801px; overflow: hidden;
    background: var(--backdrop);
    font-family: "Montserrat", sans-serif;
  }
  .stage {
    width: 1200px; height: 801px;
    display: flex; align-items: center; justify-content: center; gap: 48px;
  }
  .card {
    width: 540px; height: 309px;
    background: var(--card);
    border-bottom: 3px solid var(--accent);
    position: relative;
    box-shadow: 0 10px 28px rgba(0,0,0,.35);
  }
  /* Front */
  .brand { position: absolute; left: 44px; top: 48px; display: flex; align-items: center; gap: 16px; }
  .brand-square { width: 42px; height: 42px; border: 3px solid var(--accent); }
  .brand-name { font-weight: 800; font-size: 34px; color: var(--white); letter-spacing: 1px; line-height: 1; }
  .brand-sub { font-weight: 500; font-size: 11px; color: var(--accent); letter-spacing: 14px; margin-top: 8px; }
  .details { position: absolute; left: 44px; top: 150px; display: flex; align-items: center; gap: 22px; }
  .person-name { font-weight: 700; font-size: 20px; color: var(--accent); }
  .person-role { font-size: 13px; color: var(--white); margin-top: 4px; text-align: right; }
  .divider { width: 1px; height: 58px; background: var(--accent); opacity: .7; }
  .contacts { list-style: none; font-size: 13px; color: var(--muted); }
  .contacts li { display: flex; align-items: center; gap: 8px; line-height: 20px; }
  .contacts svg { width: 11px; height: 11px; fill: var(--accent); flex: none; }
  .address { position: absolute; left: 44px; bottom: 36px; font-size: 14px; color: var(--white); }
  /* Back */
  .back-brand { position: absolute; inset: 0; display: flex; align-items: center; justify-content: center; gap: 18px; }
  .back-brand .brand-square { width: 58px; height: 58px; border-color: var(--embossed); border-width: 4px; }
  .back-brand .brand-name { font-size: 46px; color: var(--accent-soft); }
  .back-brand .brand-sub { color: var(--embossed); font-size: 14px; letter-spacing: 18px; }
</style>
</head>
<body>
<main class="stage">
  <section class="card card-front" aria-label="Card front">
    <div class="brand">
      <div class="brand-square"></div>
      <div>
        <div class="brand-name">HALVENMOOR</div>
        <div class="brand-sub">CONSULTING</div>
      </div>
    </div>
    <div class="details">
      <div class="person">
        <div class="person-name">MAREL TOVISK</div>
        <div class="person-role">President</div>
      </div>
      <div class="divider"></div>
      <ul class="contacts">
        <li><svg viewBox="0 0 10 10"><path d="M2 0h2l1 3-1.5 1a6 6 0 0 0 2.5 2.5L7 5l3 1v2c0 1-1 2-2 2A8 8 0 0 1 0 2c0-1 1-2 2-2z"/></svg>555-014-2287</li>
        <li><svg viewBox="0 0 10 10"><path d="M0 2h10v6H0z M0 2l5 3 5-3" /></svg>marel@halvenmoor.com</li>
        <li><svg viewBox="0 0 10 10"><circle cx="5" cy="5" r="5"/></svg>www.halvenmoor.com</li>
      </ul>
    </div>
    <p class="address">3870 Wrenfield Harbor, Corvell Bay CA 90412</p>
  </section>
  <section class="card card-back" aria-label="Card back">
    <div class="back-brand">
      <div class="brand-square"></div>
      <div>
        <div class="brand-name">HALVENMOOR</div>
        <div class="brand-sub">CONSULTING</div>
      </div>
    </div>
  </section>
</main>
</body>
</html>
```